Modern Medical Optometry Website

We need mordern, Patient friendly website. Easy to navigate and enhance our advance medical technology and excellent patient care.
1. HOME PAGE
2. OUR TEAM PAGE
3. EYECARE PAGE - VISION SERVICES, EYE EXAMS, KERATOCONUS CENTER, GLAUCOMA , DIABITES, MELORIDEX EXAM, DIGITAL RETINAL, OCT.
4. MYOPIA CONTROL CLINIC
5. DRY EYE CLINIC
6. EYEWEAR
7. PATIENT CENTER - BLOG
7. CONTACT US
This is our current website www.brivaloka.com
and We want to add more content and a cleaner design like these website
http://tarnwickfolvendale.com/
https://www.qmvorlu.com/

```html
<!DOCTYPE html>
<html lang="en">
<head>
<meta charset="utf-8">
<title>Special Offers – Lumora Optometry</title>
<link rel="stylesheet" href="https://fonts.googleapis.com/css2?family=Montserrat:wght@400;600;700;800&family=Open+Sans:wght@400;600;700&display=swap">
<style>
:root{
  --yellow:#f7d21f;
  --blue:#2ea8e6;
  --teal:#1f8fc4;
  --orange:#f2a23c;
  --orange-light:#f7c06a;
  --ink:#2b2b2b;
  --muted:#8a8a8a;
  --panel:#ededed;
  --hero:#e9e9e9;
  --dark:#333333;
  --white:#ffffff;
}
*{box-sizing:border-box;margin:0;padding:0}
html,body{width:1200px;height:2696px;overflow:hidden}
body{font-family:"Open Sans",Arial,sans-serif;color:var(--ink);background:var(--white);position:relative}
.site-header{height:120px;position:relative;border-bottom:1px solid #eee}
.brand{position:absolute;left:70px;top:18px;display:flex;align-items:center;gap:12px}
.brand-mark{width:44px;height:44px;background:var(--yellow)}
.brand-name{font-family:"Montserrat",sans-serif;font-weight:700;font-size:18px;color:var(--teal);line-height:1.1;width:110px}
.top-contact{position:absolute;right:72px;top:12px;display:flex;gap:28px;font-size:13px;color:var(--muted)}
.top-contact span{display:flex;align-items:center;gap:8px}
.top-contact svg{width:14px;height:14px;fill:var(--yellow)}
.main-nav{position:absolute;right:72px;top:62px;display:flex;gap:30px;font-family:"Montserrat",sans-serif;font-size:13px;font-weight:600;text-transform:uppercase;color:#555}
.main-nav a{color:inherit;text-decoration:none;padding-bottom:8px}
.main-nav a.active{color:var(--ink);border-bottom:3px solid var(--yellow)}
.page-hero{height:300px;background:var(--hero);text-align:center;padding-top:92px}
.page-hero h1{font-family:"Montserrat",sans-serif;font-weight:800;font-size:38px;color:var(--teal);letter-spacing:1px}
.page-hero p{width:760px;margin:20px auto 0;font-size:13px;line-height:1.7;color:var(--muted)}
.offers{padding:80px 72px 0}
.offer{display:flex;height:340px;margin-bottom:80px}
.offer.reverse{flex-direction:row-reverse}
.offer-visual{width:628px;height:340px;position:relative;overflow:hidden;
  background:radial-gradient(circle at 50% 50%,var(--orange-light) 0%,var(--orange) 70%)}
.offer-badge{position:absolute;left:109px;top:-35px;width:410px;height:410px;border-radius:50%;background:var(--blue);
  color:var(--white);text-align:center;display:flex;flex-direction:column;justify-content:center;align-items:center;padding:0 60px}
.offer-badge .big{font-family:"Montserrat",sans-serif;font-weight:800;font-size:54px;line-height:1;white-space:nowrap}
.offer-badge .sub{font-family:"Montserrat",sans-serif;font-weight:700;font-size:19px;text-transform:uppercase;margin-top:12px;line-height:1.3}
.offer-badge .note{font-size:9px;margin-top:14px;line-height:1.4;width:170px;opacity:.9}
.offer-text{width:428px;background:var(--panel);padding:66px 40px 0}
.offer-text h2{font-family:"Montserrat",sans-serif;font-weight:800;font-size:30px;color:var(--teal)}
.offer-text .label{font-family:"Montserrat",sans-serif;font-size:16px;text-transform:uppercase;color:#9a9a9a;margin-top:8px}
.offer-text p{font-size:12px;line-height:1.6;color:var(--muted);margin-top:16px;width:260px}
.btn{display:inline-block;margin-top:28px;background:var(--yellow);color:var(--ink);font-family:"Montserrat",sans-serif;font-weight:700;font-size:13px;text-transform:uppercase;padding:13px 18px;text-decoration:none}
.site-footer{position:absolute;left:0;top:2220px;width:1200px;height:410px;background:var(--yellow);padding:62px 72px 0;display:flex;gap:80px}
.footer-col{width:300px}
.footer-col h3{font-family:"Montserrat",sans-serif;font-weight:700;font-size:22px;color:var(--teal);margin-bottom:28px}
.contact-line{display:flex;gap:14px;font-size:13px;color:var(--ink);margin-bottom:16px;line-height:1.5}
.contact-line svg{flex:none;width:16px;height:16px;fill:var(--teal);margin-top:2px}
.map-btn{display:inline-flex;align-items:center;gap:40px;margin-top:12px;background:var(--dark);color:var(--white);border-radius:22px;padding:11px 22px;font-size:13px;text-decoration:none}
.map-btn svg{width:12px;height:12px;fill:var(--white)}
.hours p{font-size:13px;line-height:1.9}
.hours .hint{margin-top:14px;line-height:1.5}
.social{display:flex;gap:12px;margin-top:18px}
.social span{width:34px;height:34px;border-radius:50%;background:#555}
.copyright{position:absolute;left:0;top:2630px;width:1200px;height:66px;background:var(--white);text-align:center;line-height:66px;font-size:13px;color:var(--muted)}
.copyright strong{color:var(--teal)}
</style>
</head>
<body>
<header class="site-header">
  <div class="brand"><span class="brand-mark"></span><span class="brand-name">Lumora Optometry</span></div>
  <div class="top-contact">
    <span><svg viewBox="0 0 24 24"><path d="M6.6 10.8a15 15 0 0 0 6.6 6.6l2.2-2.2c.3-.3.7-.4 1-.2 1.1.4 2.3.6 3.6.6.6 0 1 .4 1 1V20c0 .6-.4 1-1 1A17 17 0 0 1 3 4c0-.6.4-1 1-1h3.5c.6 0 1 .4 1 1 0 1.3.2 2.5.6 3.6.1.3 0 .7-.2 1z"/></svg>555-204-3181</span>
    <span><svg viewBox="0 0 24 24"><path d="M2 5h20v14H2zm2 2v.5l8 5 8-5V7z"/></svg>info@lumoraoptometry.com</span>
  </div>
  <nav class="main-nav">
    <a class="active" href="#">Home</a><a href="#">Our Team</a><a href="#">Eye Care</a><a href="#">Myopia Control Clinic</a><a href="#">Eyewear</a><a href="#">Blog</a><a href="#">Contact Us</a>
  </nav>
</header>

<section class="page-hero">
  <h1>SPECIAL OFFERS</h1>
  <p>Lorem ipsum is simply dummy text of the printing and typesetting industry. Lorem Ipsum has been the industry's standard dummy text ever since the 1500s, when an unknown printer took a galley of type and scrambled it to make a type specimen book.</p>
</section>

<main class="offers">
  <article class="offer">
    <div class="offer-visual" role="img" aria-label="Orange sunburst backdrop behind the offer badge">
      <div class="offer-badge"><span class="big">10% OFF</span><span class="sub">Prescription Glasses</span><span class="note">Walk-ins welcome. We are open six days a week including all Saturdays.</span></div>
    </div>
    <div class="offer-text">
      <h2>10% OFF</h2><div class="label">Prescription Glasses</div>
      <p>Walk-ins welcome. We are open six days a week including all Saturdays.</p>
      <a class="btn" href="#">Make an appointment</a>
    </div>
  </article>

  <article class="offer reverse">
    <div class="offer-visual" role="img" aria-label="Orange sunburst backdrop behind the offer badge">
      <div class="offer-badge"><span class="big">30% OFF</span><span class="sub">Children Prescription Glasses</span><span class="note">Walk-ins welcome. We are open six days a week including all Saturdays.</span></div>
    </div>
    <div class="offer-text">
      <h2>30% OFF</h2><div class="label">Children Prescription Glasses</div>
      <p>Walk-ins welcome. We are open six days a week including all Saturdays.</p>
      <a class="btn" href="#">Make an appointment</a>
    </div>
  </article>

  <article class="offer">
    <div class="offer-visual" role="img" aria-label="Orange sunburst backdrop behind the offer badge">
      <div class="offer-badge"><span class="big">FREE LENS</span><span class="sub">On Second Pair Glasses</span><span class="note">Walk-ins welcome. We are open six days a week including all Saturdays.</span></div>
    </div>
    <div class="offer-text">
      <h2>FREE LENS</h2><div class="label">On Second Pair Glasses</div>
      <p>Walk-ins welcome. We are open six days a week including all Saturdays.</p>
      <a class="btn" href="#">Make an appointment</a>
    </div>
  </article>

  <article class="offer reverse">
    <div class="offer-visual" role="img" aria-label="Orange sunburst backdrop behind the offer badge">
      <div class="offer-badge"><span class="big">$10</span><span class="sub">First Time Contact Lens Exam</span><span class="note">Walk-ins welcome. We are open six days a week including all Saturdays.</span></div>
    </div>
    <div class="offer-text">
      <h2>$10 FIRST TIME</h2><div class="label">Contact Lens Exam</div>
      <p>Walk-ins welcome. We are open six days a week including all Saturdays.</p>
      <a class="btn" href="#">Make an appointment</a>
    </div>
  </article>
</main>

<footer class="site-footer">
  <div class="footer-col">
    <h3>Lumora Optometry</h3>
    <div class="contact-line"><svg viewBox="0 0 24 24"><path d="M6.6 10.8a15 15 0 0 0 6.6 6.6l2.2-2.2c.3-.3.7-.4 1-.2 1.1.4 2.3.6 3.6.6.6 0 1 .4 1 1V20c0 .6-.4 1-1 1A17 17 0 0 1 3 4c0-.6.4-1 1-1h3.5c.6 0 1 .4 1 1 0 1.3.2 2.5.6 3.6.1.3 0 .7-.2 1z"/></svg>555-204-3181</div>
    <div class="contact-line"><svg viewBox="0 0 24 24"><path d="M6.6 10.8a15 15 0 0 0 6.6 6.6l2.2-2.2c.3-.3.7-.4 1-.2 1.1.4 2.3.6 3.6.6.6 0 1 .4 1 1V20c0 .6-.4 1-1 1A17 17 0 0 1 3 4c0-.6.4-1 1-1h3.5c.6 0 1 .4 1 1 0 1.3.2 2.5.6 3.6.1.3 0 .7-.2 1z"/></svg>555-204-3190</div>
    <div class="contact-line"><svg viewBox="0 0 24 24"><path d="M2 5h20v14H2zm2 2v.5l8 5 8-5V7z"/></svg>info@lumoraoptometry.com</div>
    <div class="contact-line"><svg viewBox="0 0 24 24"><path d="M12 2a7 7 0 0 0-7 7c0 5 7 13 7 13s7-8 7-13a7 7 0 0 0-7-7zm0 9.5A2.5 2.5 0 1 1 12 6.5a2.5 2.5 0 0 1 0 5z"/></svg>4120 Alder Park Blvd,<br>Fenmoor, OR 97020</div>
    <a class="map-btn" href="#">Get directions on the map <svg viewBox="0 0 12 12"><path d="M3 1l6 5-6 5z"/></svg></a>
  </div>
  <div class="footer-col">
    <h3>Brookhaven Vale</h3>
    <div class="contact-line"><svg viewBox="0 0 24 24"><path d="M6.6 10.8a15 15 0 0 0 6.6 6.6l2.2-2.2c.3-.3.7-.4 1-.2 1.1.4 2.3.6 3.6.6.6 0 1 .4 1 1V20c0 .6-.4 1-1 1A17 17 0 0 1 3 4c0-.6.4-1 1-1h3.5c.6 0 1 .4 1 1 0 1.3.2 2.5.6 3.6.1.3 0 .7-.2 1z"/></svg>555-318-6624</div>
    <div class="contact-line"><svg viewBox="0 0 24 24"><path d="M2 5h20v14H2zm2 2v.5l8 5 8-5V7z"/></svg>brookhaven@lumoraoptometry.com</div>
    <div class="contact-line"><svg viewBox="0 0 24 24"><path d="M12 2a7 7 0 0 0-7 7c0 5 7 13 7 13s7-8 7-13a7 7 0 0 0-7-7zm0 9.5A2.5 2.5 0 1 1 12 6.5a2.5 2.5 0 0 1 0 5z"/></svg>8723 Quillan Ave, Suite 12,<br>Brookhaven Vale, NV 89410</div>
    <a class="map-btn" href="#">Get directions on the map <svg viewBox="0 0 12 12"><path d="M3 1l6 5-6 5z"/></svg></a>
  </div>
  <div class="footer-col hours">
    <h3>Opening Hours</h3>
    <p>Monday - Thursday : <strong>8 am - 6 pm</strong></p>
    <p>Friday : <strong>8:30 am - 5 pm</strong></p>
    <p>Saturday : <strong>8:30 am - 5 pm</strong></p>
    <p>Closed on <strong>Sundays</strong></p>
    <p class="hint">Please keep in mind we are closed<br>for <strong>lunch 1-2 pm</strong></p>
    <div class="social"><span></span><span></span><span></span><span></span></div>
  </div>
</footer>
<div class="copyright">Copyright © <strong>LUMORA OPTOMETRY</strong> - 2016 - All Rights Reserved</div>
</body>
</html>
```